Corvel Capital LLC

Need Professional Business cards for New Investment Fund

Target Market(s)

High Quality investors

Industry/Entity Type

Financial

Contact Information for Business Card

Phone Number +1 555 284 6190
Name Lukas Varenko
Title Fund Manager
email lv@FundCorvel.com
Website www.FundCorvel.com

Colors

Designer to choose colors to be used in the design.

Requirements
Must have
• Must have our Logo and all of the above. Must be made so lettering and loge can be raised

```html
<!DOCTYPE html>
<html lang="en">
<head>
<meta charset="utf-8">
<title>Corvel Capital LLC – Business Card</title>
<link rel="stylesheet" href="https://fonts.googleapis.com/css2?family=Jost:wght@400;500;600;700&display=swap">
<style>
  :root {
    --backdrop: #dcdcdc;
    --paper: #ffffff;
    --brand-green: #22ee00;
    --ink-dark: #4a4f48;
    --ink-text: #4d4d4d;
  }
  html, body {
    margin: 0;
    width: 1200px;
    height: 1200px;
    overflow: hidden;
    background: var(--backdrop);
    font-family: "Jost", sans-serif;
  }
  .canvas {
    position: relative;
    width: 1200px;
    height: 1200px;
  }
  .card {
    position: absolute;
    left: 262px;
    width: 686px;
    height: 392px;
    overflow: hidden;
  }
  .card--front { top: 165px; background: var(--paper); }
  .card--back { top: 653px; background: var(--brand-green); }

  .brand-mark {
    position: absolute;
    display: flex;
    align-items: center;
    gap: 10px;
    font-weight: 600;
    letter-spacing: 0.04em;
    white-space: nowrap;
    color: var(--ink-dark);
    text-transform: uppercase;
  }
  .brand-mark__square {
    display: block;
    flex: none;
    background: var(--brand-green);
  }
  .card--front .brand-mark {
    right: 44px;
    top: 150px;
    font-size: 24px;
  }
  .card--front .brand-mark__square { width: 16px; height: 16px; }
  .card--back .brand-mark {
    left: 0; right: 0; top: 172px;
    justify-content: center;
    font-size: 40px;
  }
  .card--back .brand-mark__square { width: 24px; height: 24px; background: var(--ink-dark); }

  .holder-name {
    position: absolute;
    left: 36px;
    top: 237px;
    margin: 0;
    font-size: 25px;
    font-weight: 700;
    letter-spacing: 0.01em;
    color: var(--brand-green);
    text-transform: uppercase;
  }
  .holder-title {
    position: absolute;
    left: 36px;
    top: 266px;
    margin: 0;
    font-size: 16px;
    font-weight: 600;
    color: var(--ink-dark);
  }
  .divider {
    position: absolute;
    left: 38px;
    top: 298px;
    width: 605px;
    height: 1px;
    background: var(--ink-dark);
  }
  .contact {
    position: absolute;
    left: 36px;
    top: 315px;
    margin: 0;
    padding: 0;
    list-style: none;
    font-size: 16px;
    color: var(--ink-text);
  }
  .contact li {
    display: flex;
    align-items: center;
    gap: 10px;
    height: 21px;
  }
  .contact svg { width: 13px; height: 13px; fill: var(--brand-green); }

  .footer-band {
    position: absolute;
    left: 0;
    bottom: 0;
    width: 686px;
    height: 30px;
  }
  .website {
    position: absolute;
    right: 32px;
    bottom: 8px;
    font-size: 15px;
    font-weight: 500;
    letter-spacing: 0.12em;
    color: #ffffff;
  }
</style>
</head>
<body>
<main class="canvas">

  <section class="card card--front" aria-label="Business card front">
    <div class="brand-mark">
      <span class="brand-mark__square"></span>
      <span>Corvel Capital</span>
    </div>

    <h1 class="holder-name">Lukas Varenko</h1>
    <p class="holder-title">Fund Manager</p>
    <div class="divider"></div>

    <ul class="contact">
      <li>
        <svg viewBox="0 0 24 24" aria-hidden="true"><path d="M6.6 10.8a15.1 15.1 0 0 0 6.6 6.6l2.2-2.2a1 1 0 0 1 1-.25 11.4 11.4 0 0 0 3.6.57 1 1 0 0 1 1 1V20a1 1 0 0 1-1 1A17 17 0 0 1 3 4a1 1 0 0 1 1-1h3.5a1 1 0 0 1 1 1c0 1.25.2 2.45.57 3.57a1 1 0 0 1-.25 1z"/></svg>
        <span>+1 555 284 6190</span>
      </li>
      <li>
        <svg viewBox="0 0 24 24" aria-hidden="true"><path d="M2 5h20v14H2z M2 5l10 8 10-8" /></svg>
        <span>lv@FundCorvel.com</span>
      </li>
    </ul>

    <svg class="footer-band" viewBox="0 0 686 30" aria-hidden="true">
      <polygon points="0,11 412,11 408,15 0,15" fill="var(--brand-green)"/>
      <polygon points="0,23 686,23 686,30 0,30" fill="var(--ink-dark)"/>
      <polygon points="429,1 686,1 686,30 400,30" fill="var(--ink-dark)"/>
    </svg>
    <span class="website">www.FundCorvel.com</span>
  </section>

  <section class="card card--back" aria-label="Business card back">
    <div class="brand-mark">
      <span class="brand-mark__square"></span>
      <span>Corvel Capital</span>
    </div>
  </section>

</main>
</body>
</html>
```